Fitness Equipment & Service

I want to make the card eye catching and fun. We are called Corvane Motion Limited and we are based in Wales. We sell, install and service all types of fitness equipment from Skipping ropes, right through the Dumbbells, Kettle bells and Barbells through to state of the art Treadmills, Running Machines and Strength Equipment. We also design and install changing room furniture and lockers.

TYPOGRAPHY
We would like to use Futrura. Futura has an appearance of efficiency and forwardness. The typeface is derived
from simple geometric forms (near-perfect circles, triangles and squares) and is based on strokes of
near-even weight, which are low in contrast. This is most visible in the almost perfectly round stroke of
the o, which is nonetheless slightly ovoid.
The lowercase has tall ascenders, which rise above the cap line. The uppercase
characters present proportions similar to those of classical Roman capitals.

TYPOGRAPHIC CONSIDERATIONS
No Strike though
No Horizontal Scaling
No Drop Shadows
No Effects
Never use less than 120% Leading

OUR CORPORATE COLOURS
BRAND GUIDELINES
We were thinking that our primary colour palette consists of the Acid Green (Pantone 382) and Process Black.

We work closely with tquarly Ltd and would like to include their name on the card somewhere. I have attached images of the other brands that we work with as an idea or the small icons I have included that illustrate what we do?. I have very kindly been given permission to use any of the images off the files that I have included below, so I hope these help. I will include these below. I would be open to suggestions if it made the card more striking Can you do it?
Updates

Hi All, Just wanted to add a few thoughts but you are the guys with the creative visions (thats why are here) We are based in Wales, UK and we would be open to lots of different ideas on a theme but must be eye catching, Bold and FUN. If you can or think that the Welsh or any dragon could be put in there then go for it (its not a must have) We have also added some ideas for colour but again its over to you!! GO FOR IT ! Thanks and look forward to your visions! Owen

Hi All, Just thought I would sen through the contact details that need to be on the card. (if you want to play around with icons instead of the wording twitter, Facebook, go for it): Corvane Motion Limited Owen Pritchard Managing Director Mob: +44 (0)7582 913 406 e-mail: sales@corvanemotion.co.uk Web: Corvanemotion.co.uk twitter: @motionLetterbin Facebook: Corvane Motion Limited

```html
<!DOCTYPE html>
<html lang="en">
<head>
<meta charset="utf-8">
<title>Corvane Motion Limited – Business Card</title>
<link href="https://fonts.googleapis.com/css2?family=Jost:wght@400;500;700&display=swap" rel="stylesheet">
<style>
  :root {
    --backdrop: #e9e8e2;
    --card-white: #ffffff;
    --acid-light: #d4e42a;
    --acid: #c4d600;
    --acid-dark: #8f9c00;
    --black-soft: #2b2b2b;
    --black: #0d0d0d;
    --text-light: #ffffff;
    --text-grey: #555555;
    --ring: #e4e4e4;
  }
  * { box-sizing: border-box; margin: 0; padding: 0; }
  html, body { width: 1200px; height: 950px; overflow: hidden; }
  body {
    background: var(--backdrop);
    font-family: "Jost", "Futura", Arial, sans-serif;
    position: relative;
  }
  .card {
    position: absolute;
    left: 250px;
    width: 700px;
    height: 400px;
    border-radius: 4px;
    overflow: hidden;
    box-shadow: 0 6px 18px rgba(0,0,0,0.18);
  }

  /* Back side */
  .card-back {
    top: 45px;
    background: linear-gradient(100deg, var(--acid-light) 0%, var(--acid) 50%, var(--acid-dark) 100%);
    text-align: center;
  }
  .card-back .emblem {
    width: 110px; height: 110px;
    margin: 70px auto 18px;
    border-radius: 50%;
    background: var(--black);
    border: 5px solid var(--ring);
  }
  .card-back .brand-name {
    font-size: 24px;
    font-weight: 700;
    color: var(--black);
    line-height: 1.2;
    text-transform: uppercase;
    letter-spacing: 1px;
  }
  .card-back .web {
    margin-top: 22px;
    color: var(--black);
    font-size: 17px;
    line-height: 1.3;
    letter-spacing: 0.5px;
  }
  .card-back .web::after {
    content: "";
    display: inline-block;
    width: 40px; height: 1px;
    background: var(--black);
    vertical-align: middle;
    margin-left: 8px;
  }

  /* Front side */
  .card-front {
    top: 505px;
    background: var(--card-white);
  }
  .contact-panel {
    position: absolute;
    left: 0; top: 30px;
    width: 360px; height: 320px;
    background: linear-gradient(135deg, var(--black-soft) 0%, var(--black) 100%);
    color: var(--text-light);
    padding: 26px 20px 0 30px;
  }
  .person-name { font-size: 26px; font-weight: 700; line-height: 1.2; color: var(--acid); }
  .person-role { font-size: 17px; line-height: 1.3; margin-bottom: 12px; }
  .address { font-size: 16px; line-height: 1.3; margin-bottom: 8px; }
  .contact-list { list-style: none; font-size: 16px; }
  .contact-list li { display: flex; align-items: center; gap: 9px; line-height: 1.4; }
  .contact-list svg, .contact-list .mark { width: 14px; height: 14px; flex: none; }
  .contact-list .mark { background: var(--acid); border-radius: 2px; }
  .contact-list .mark.round { border-radius: 50%; }

  .brand {
    position: absolute;
    left: 400px; top: 70px;
    width: 260px;
    text-align: center;
  }
  .brand .emblem {
    width: 120px; height: 120px;
    margin: 0 auto 22px;
    border-radius: 50%;
    background: var(--acid);
    border: 5px solid var(--ring);
  }
  .brand .brand-name {
    font-size: 22px;
    font-weight: 700;
    color: var(--black);
    line-height: 1.2;
    text-transform: uppercase;
    letter-spacing: 0.5px;
  }
  .brand .partner {
    margin-top: 14px;
    font-size: 14px;
    line-height: 1.3;
    color: var(--text-grey);
  }
  .acid-edge {
    position: absolute;
    right: 0; top: 55px;
    width: 14px; height: 290px;
    background: linear-gradient(180deg, var(--acid-light), var(--acid-dark));
  }
</style>
</head>
<body>

  <section class="card card-back" aria-label="Card back">
    <div class="emblem"></div>
    <p class="brand-name">Corvane Motion Limited</p>
    <p class="web">www.corvanemotion.co.uk</p>
  </section>

  <section class="card card-front" aria-label="Card front">
    <div class="contact-panel">
      <p class="person-name">Owen Pritchard</p>
      <p class="person-role">Managing Director</p>
      <p class="address">Unit 7 Heol Derwen<br>Pontyfelin, Wales CF83 4QT</p>
      <ul class="contact-list">
        <li>
          <svg viewBox="0 0 14 14" aria-hidden="true"><rect x="3" y="0.5" width="8" height="13" rx="1.5" fill="none" stroke="#c4d600" stroke-width="1.4"/><circle cx="7" cy="11" r="0.9" fill="#c4d600"/></svg>
          +44 (0)7582 913 406
        </li>
        <li>
          <svg viewBox="0 0 14 14" aria-hidden="true"><rect x="0.5" y="2.5" width="13" height="9" fill="#c4d600"/><path d="M0.5 2.5 L7 8 L13.5 2.5" fill="none" stroke="#0d0d0d" stroke-width="1"/></svg>
          sales@corvanemotion.co.uk
        </li>
        <li><span class="mark round"></span>Corvanemotion.co.uk</li>
        <li><span class="mark"></span>@motionLetterbin</li>
        <li><span class="mark"></span>Corvane Motion Limited</li>
      </ul>
    </div>

    <div class="brand">
      <div class="emblem"></div>
      <p class="brand-name">Corvane Motion Limited</p>
      <p class="partner">Working with tquarly Ltd</p>
    </div>

    <div class="acid-edge"></div>
  </section>

</body>
</html>
```